Business Card Design

Company is a Commercial Building Company specialising in New Construction and existing refurbishments

Industry/Entity Type

Business

Contact Information for Business Card

Liam Porter
Construction Manager
E Liam@marshbuilding.com.au
M 0400 213 594
Mail 14 Tarrant Rise Harbourvale WA 6180

```html
<!DOCTYPE html>
<html lang="en">
<head>
<meta charset="utf-8">
<title>Marsh Building &amp; Construction – Business Card</title>
<link href="https://fonts.googleapis.com/css2?family=Michroma&family=Questrial&display=swap" rel="stylesheet">
<style>
  :root {
    --cyan: #00b8d8;
    --cyan-light: #6fd0e6;
    --orange: #f58a1f;
    --ink: #2e3440;
    --grey: #555b63;
    --paper: #ffffff;
    --backdrop: #e9e7e4;
  }
  * { margin: 0; padding: 0; box-sizing: border-box; }
  html, body {
    width: 1200px; height: 997px; overflow: hidden;
    background: var(--backdrop);
  }
  .sheet {
    width: 1200px; height: 997px;
    display: flex; flex-direction: column;
    align-items: center; justify-content: center; gap: 60px;
  }
  .card {
    position: relative;
    width: 700px; height: 400px;
    overflow: hidden;
    box-shadow: 0 6px 18px rgba(0,0,0,0.12);
  }

  /* Front */
  .card-front {
    background: radial-gradient(ellipse at 55% 45%, var(--cyan-light) 0%, var(--cyan) 75%);
    color: var(--paper);
  }
  .front-wordmark {
    position: absolute; left: 90px; top: 140px;
    font-family: "Michroma", sans-serif;
    line-height: 1.2;
  }
  .front-wordmark .line-main { font-size: 40px; letter-spacing: 0.5px; }
  .front-wordmark .line-sub { font-size: 40px; letter-spacing: 0.5px; }

  /* Back */
  .card-back { background: var(--paper); font-family: "Questrial", sans-serif; }
  .card-back .swoosh { position: absolute; inset: 0; }
  .brand {
    position: absolute; left: 60px; top: 140px;
    display: flex; align-items: center; gap: 12px;
  }
  .brand-square { width: 26px; height: 26px; background: var(--cyan); }
  .brand-name {
    font-family: "Michroma", sans-serif;
    font-size: 15px; line-height: 1.3; color: var(--ink);
  }
  .person { position: absolute; left: 60px; top: 232px; }
  .person-name { color: var(--orange); font-size: 30px; letter-spacing: 1px; text-transform: uppercase; }
  .person-title { color: var(--grey); font-size: 15px; margin-top: 2px; }
  .contact { position: absolute; left: 60px; top: 305px; list-style: none; }
  .contact li, .address {
    display: flex; align-items: center; gap: 10px;
    color: var(--ink); font-size: 18px; line-height: 1.5;
  }
  .contact svg, .address svg { flex: none; }
  .address { position: absolute; left: 405px; top: 218px; align-items: flex-start; }
  .address svg { margin-top: 5px; }
</style>
</head>
<body>
<main class="sheet">
  <section class="card card-front">
    <div class="front-wordmark">
      <div class="line-main">MARSH BUILDING</div>
      <div class="line-sub">&amp; CONSTRUCTION</div>
    </div>
  </section>

  <section class="card card-back">
    <svg class="swoosh" width="700" height="400" viewBox="0 0 700 400">
      <path d="M300 0 H700 V290 C690 130 560 30 300 0 Z" fill="var(--cyan)"/>
      <path d="M230 28 C500 45 668 150 676 300" fill="none" stroke="var(--orange)" stroke-width="5"/>
    </svg>

    <div class="brand">
      <span class="brand-square"></span>
      <div class="brand-name">MARSH BUILDING<br>&amp; CONSTRUCTION</div>
    </div>

    <div class="person">
      <div class="person-name">Liam Porter</div>
      <div class="person-title">Construction Manager</div>
    </div>

    <ul class="contact">
      <li>
        <svg width="14" height="14" viewBox="0 0 14 14"><rect x="1.5" y="1.5" width="11" height="11" rx="2" fill="none" stroke="var(--orange)" stroke-width="2"/></svg>
        0400 213 594
      </li>
      <li>
        <svg width="14" height="12" viewBox="0 0 14 12"><rect x="1" y="1" width="12" height="10" fill="var(--orange)"/><path d="M1 1 L7 7 L13 1" fill="none" stroke="#fff" stroke-width="1.4"/></svg>
        Liam@marshbuilding.com.au
      </li>
    </ul>

    <div class="address">
      <svg width="12" height="16" viewBox="0 0 12 16"><path d="M6 15 C2 10 1 8 1 6 A5 5 0 0 1 11 6 C11 8 10 10 6 15 Z" fill="none" stroke="var(--orange)" stroke-width="2"/></svg>
      <div>14 Tarrant Rise<br>Harbourvale WA 6180</div>
    </div>
  </section>
</main>
</body>
</html>
```